Kelvor Engineers: Why you should hire us keepsake

New design. Open to plastic cards. We are an engineering firm that designs cell phone towers and commercial buildings. Please check out our website www.kelvorstruct.com for more details. We want people to remember our card and for it to be useful if possible. We want the same look and feel on these cards to be translated to other marketing material we may need such as brochures.

Target Market(s)

Architects, Developers and Telecommunication Carriers

Industry/Entity Type

Engineering

Contact Information for Business Card

Card with our company colors, logo, and innovative design with elements related to our industry.

Font styles to use
Sans Serif

Colors
9bcb3c
abd036
0255a3

Requirements
Must have
• Sleek and hip design
Nice to have
• Bright lime green and navy coloring that pops with an innovative design.
Should not have
• A basic and boring design

```html
<!DOCTYPE html>
<html lang="en">
<head>
<meta charset="utf-8">
<title>Kelvor Engineers – Business Card</title>
<link rel="stylesheet" href="https://fonts.googleapis.com/css2?family=Work+Sans:wght@400;500;700;800&display=swap">
<style>
  :root {
    --navy: #0f2650;
    --lime: #3fd43a;
    --white: #ffffff;
    --stage: #2b2b2d;
  }
  * { margin: 0; padding: 0; box-sizing: border-box; }
  html, body { width: 1200px; height: 900px; overflow: hidden; }
  body {
    background: var(--stage);
    font-family: "Work Sans", Arial, sans-serif;
    position: relative;
  }
  .card {
    position: absolute;
    width: 540px;
    height: 310px;
    border-radius: 22px;
    overflow: hidden;
    background: var(--white);
    box-shadow: 0 14px 30px rgba(0,0,0,0.45);
  }
  .card svg.swoosh { position: absolute; inset: 0; width: 100%; height: 100%; }
  .card-front { left: 60px; top: 110px; }
  .card-back { left: 600px; top: 480px; }

  .brand {
    position: absolute;
    left: 190px;
    top: 122px;
    width: 330px;
    text-align: center;
  }
  .brand-name {
    color: var(--lime);
    font-weight: 800;
    font-size: 38px;
    line-height: 1;
    letter-spacing: -0.5px;
    white-space: nowrap;
  }
  .brand-cities {
    margin-top: 14px;
    color: var(--navy);
    font-weight: 500;
    font-size: 11px;
    letter-spacing: 0.8px;
    white-space: nowrap;
  }
  .brand-cities .sep { color: var(--lime); margin: 0 4px; }

  .contact {
    position: absolute;
    left: 0;
    top: 150px;
  }
  .contact-head {
    border-left: 4px solid var(--lime);
    padding-left: 40px;
  }
  .person-name {
    color: var(--navy);
    font-weight: 500;
    font-size: 24px;
    line-height: 1.1;
    white-space: nowrap;
  }
  .person-role {
    color: var(--lime);
    font-size: 16px;
    line-height: 1.2;
  }
  .contact-list { list-style: none; margin-top: 10px; padding-left: 40px; }
  .contact-list li {
    display: flex;
    align-items: center;
    gap: 8px;
    color: var(--navy);
    font-size: 16px;
    line-height: 1.4;
    white-space: nowrap;
  }
  .contact-list svg { width: 11px; height: 11px; flex: none; }
</style>
</head>
<body>

<section class="card card-front" aria-label="Business card front">
  <svg class="swoosh" viewBox="0 0 540 310" preserveAspectRatio="none" aria-hidden="true">
    <rect width="540" height="310" fill="var(--navy)"/>
    <circle cx="320" cy="160" r="300" fill="var(--lime)"/>
    <circle cx="340" cy="145" r="292" fill="var(--white)"/>
    <circle cx="350" cy="138" r="286" fill="var(--navy)"/>
    <circle cx="362" cy="126" r="282" fill="var(--lime)"/>
    <circle cx="372" cy="118" r="276" fill="var(--white)"/>
  </svg>
  <div class="brand">
    <div class="brand-name">Kelvor Engineers</div>
    <div class="brand-cities">RIVERTON<span class="sep">|</span>OAKDALE<span class="sep">|</span>FAIRMONT<span class="sep">|</span>WESTBROOK</div>
  </div>
</section>

<section class="card card-back" aria-label="Business card back">
  <svg class="swoosh" viewBox="0 0 540 310" preserveAspectRatio="none" aria-hidden="true">
    <g transform="translate(540 310) scale(-1 -1)">
      <rect width="540" height="310" fill="var(--navy)"/>
      <circle cx="320" cy="160" r="300" fill="var(--lime)"/>
      <circle cx="340" cy="145" r="292" fill="var(--white)"/>
      <circle cx="350" cy="138" r="286" fill="var(--navy)"/>
      <circle cx="362" cy="126" r="282" fill="var(--lime)"/>
      <circle cx="372" cy="118" r="276" fill="var(--white)"/>
    </g>
  </svg>
  <div class="contact">
    <div class="contact-head">
      <div class="person-name">Dana Whitfield Carron</div>
      <div class="person-role">Director</div>
    </div>
    <ul class="contact-list">
      <li>
        <svg viewBox="0 0 12 12"><path d="M2 1l2 0 1 3-1.5 1a6 6 0 0 0 3 3L7.5 6.5l3 1v2l-1 1C5 10.5 1.5 7 1 2z" fill="var(--lime)"/></svg>
        555.201.4470
      </li>
      <li>
        <svg viewBox="0 0 12 12"><rect x="3" y="0.5" width="6" height="11" rx="1.2" fill="none" stroke="var(--lime)" stroke-width="1.4"/><circle cx="6" cy="9.3" r="0.8" fill="var(--lime)"/></svg>
        555.318.6624
      </li>
      <li>
        <svg viewBox="0 0 12 12"><rect x="0.7" y="2.2" width="10.6" height="7.6" rx="1" fill="none" stroke="var(--lime)" stroke-width="1.4"/><path d="M1 2.8l5 4 5-4" fill="none" stroke="var(--lime)" stroke-width="1.4"/></svg>
        dcarron@kelvorstruct.com
      </li>
      <li>
        <svg viewBox="0 0 12 12"><circle cx="6" cy="6" r="5" fill="none" stroke="var(--lime)" stroke-width="1.3"/><ellipse cx="6" cy="6" rx="2.2" ry="5" fill="none" stroke="var(--lime)" stroke-width="1"/><path d="M1 6h10" stroke="var(--lime)" stroke-width="1"/></svg>
        www.kelvorstruct.com
      </li>
    </ul>
  </div>
</section>

</body>
</html>
```